ORIM Holding

ORIM holding is located in the UAE. In the company, there are several departments covering Hospitality management, Facility Management, interior design and Construction.

The logo should not include the name holding, Just ORIM.

Needed Items:

(1) Logo.
(2) Business Card.
(3) Letterhead
(4) Envelope
(5) cd cover
(6) email signature
Updates

The previous brief was misplaced with another competition. Current update is the final.

Target Market(s)

Collaboration with international high end firms.

Industry/Entity Type

Business

Requirements
Must have
• COLOR PREFERENCE Maximum 2 colors, preferably mono-color with different shades.
Nice to have
• Elegant, luxurious, and minimalistic.

```html
<!DOCTYPE html>
<html lang="en">
<head>
<meta charset="utf-8">
<title>ORIM Holding — Business Card</title>
<link rel="stylesheet" href="https://fonts.googleapis.com/css2?family=Cinzel:wght@400;600&family=Arimo:wght@400&display=swap">
<style>
  :root {
    --bg: #2f2f2f;
    --red: #a50006;
    --red-deep: #6a0004;
    --red-dark: #7a0a0e;
    --paper: #ffffff;
    --ink: #2b2b2b;
    --rule: #d8d8d8;
  }
  * { margin: 0; padding: 0; box-sizing: border-box; }
  html, body { width: 1200px; height: 866px; overflow: hidden; background: var(--bg); }
  .stage {
    width: 1200px; height: 866px;
    display: flex; align-items: center; justify-content: center; gap: 60px;
  }
  .card {
    width: 525px; height: 300px; position: relative;
    box-shadow: 0 14px 30px rgba(0,0,0,.45);
  }
  .card-front {
    background: radial-gradient(ellipse at 40% 35%, #b3050b 0%, var(--red) 40%, var(--red-deep) 100%);
    display: flex; flex-direction: column; align-items: center; justify-content: center; gap: 18px;
  }
  .front-mark {
    width: 70px; height: 70px; border-radius: 50%;
    border: 2px solid rgba(255,255,255,.9);
  }
  .front-brand {
    font-family: "Cinzel", serif; font-weight: 400; font-size: 34px;
    letter-spacing: 3px; color: var(--paper);
  }
  .card-back { background: var(--paper); padding: 48px 36px 0 38px; }
  .back-brand {
    position: absolute; top: 74px; right: 34px;
    font-family: "Cinzel", serif; font-weight: 400; font-size: 26px;
    letter-spacing: 2px; color: var(--red-dark);
  }
  .person-name {
    font-family: "Cinzel", serif; font-weight: 400; font-size: 21px;
    letter-spacing: 1.5px; color: var(--red-dark);
  }
  .person-title {
    font-family: "Arimo", sans-serif; font-size: 12px; color: var(--ink);
    margin-top: 2px; letter-spacing: .5px;
  }
  .contact-list { list-style: none; margin-top: 14px; }
  .contact-list li {
    font-family: "Arimo", sans-serif; font-size: 12px; color: var(--ink);
    display: flex; align-items: center; gap: 7px; line-height: 18px; letter-spacing: .4px;
  }
  .contact-list svg { width: 11px; height: 11px; fill: var(--red); flex: none; }
  .divider {
    position: absolute; left: 38px; right: 34px; top: 212px;
    height: 1px; background: var(--rule);
  }
  .address {
    position: absolute; right: 34px; bottom: 30px; text-align: right;
    font-family: "Arimo", sans-serif; font-size: 12px; font-style: normal; color: var(--ink);
    line-height: 17px; letter-spacing: .4px;
  }
</style>
</head>
<body>
<main class="stage">
  <section class="card card-front" aria-label="Card front">
    <div class="front-mark"></div>
    <div class="front-brand">ORIM HOLDING</div>
  </section>

  <section class="card card-back" aria-label="Card back">
    <div class="back-brand">ORIM HOLDING</div>
    <h1 class="person-name">DANIEL HAYES</h1>
    <p class="person-title">Managing Director</p>
    <ul class="contact-list">
      <li>
        <svg viewBox="0 0 24 24" aria-hidden="true"><path d="M6.6 10.8a15.1 15.1 0 0 0 6.6 6.6l2.2-2.2a1 1 0 0 1 1-.25 11.4 11.4 0 0 0 3.6.57 1 1 0 0 1 1 1V20a1 1 0 0 1-1 1A17 17 0 0 1 3 4a1 1 0 0 1 1-1h3.5a1 1 0 0 1 1 1c0 1.25.2 2.45.57 3.57a1 1 0 0 1-.25 1z"/></svg>
        044-555 010 200
      </li>
      <li>
        <svg viewBox="0 0 24 24" aria-hidden="true"><path d="M2 5h20v14H2z"/><path d="M3 6l9 7 9-7" fill="none" stroke="#fff" stroke-width="1.6"/></svg>
        info@orimmail.com
      </li>
      <li>
        <svg viewBox="0 0 24 24" aria-hidden="true"><circle cx="12" cy="12" r="10"/><path d="M2 12h20M12 2c3 3 3 17 0 20M12 2c-3 3-3 17 0 20M4 7h16M4 17h16" fill="none" stroke="#fff" stroke-width="1.3"/></svg>
        www.orimgroup.com
      </li>
    </ul>
    <div class="divider"></div>
    <address class="address">
      18, Marina Walk Tower B<br>PO Box 7731, Dubai UAE
    </address>
  </section>
</main>
</body>
</html>
```